Mortgage and Asset Finance Broker Needs a Wordpress Website Design

I need a modern looking Wordpress website to showcase my service as a mortgage and asset broker. I have a company and we work with various lenders to arrange mortgages, as well as commercial lending and business asset finance. The website needs to look professional, be easy to navigate and capture leads. SEO is obviously very important to me. It really needs to be something that shows trust and professioanlism.
Updates

On the home page I will need to have some boxes for Home Loans, Refinancing, Business (and Agriculture) Loans etc. I'd like a carousel in the middle which shows our lenders (so that can have the banks logos added).

It needs to be easy top navigate and showcase all we do - Home Loans, Refinancing, Commercial Loans, Car Loans, Asset Finance etc.

There are plenty of companies on the internet that do this.

There is some good information here https://lendplatehq.com.au/mortgage-broker-homepage/

I need to make sure that editing the website is easy (I think Wordpress has something that allows that).

Also we are very much an Australian business so that is something to advertise.

Industry/Entity Type

Mortgage and Finance Broker

Coding

Coded - Design and coding required

Number of Pages Required

5+ page

Requirements
Must have
• Easy to navigate professional feel. Must be responsive and mobile friendly.
Nice to have
• Homepage with links to inner pages. Contact buttons.

```html
<!DOCTYPE html>
<html lang="en">
<head>
<meta charset="utf-8">
<title>Vantora Financial Services – Mortgage &amp; Asset Finance Broker</title>
<link href="https://fonts.googleapis.com/css2?family=Montserrat:wght@500;600;700;800;900&family=Mulish:wght@400;600;700&display=swap" rel="stylesheet">
<style>
:root{
  --magenta:#d6145c;
  --purple:#5a2a88;
  --blue:#1c4c9e;
  --blue-dark:#163d82;
  --orange:#f5821f;
  --ink:#1c1c24;
  --text:#5d5f6b;
  --line:#e4e5ea;
  --soft:#f3f4f7;
  --black:#0d0d10;
  --white:#ffffff;
}
*{box-sizing:border-box;margin:0;padding:0}
html,body{width:1200px;height:4968px;overflow:hidden}
body{font-family:'Mulish',sans-serif;color:var(--text);background:var(--white);position:relative}
h1,h2,h3,h4,.btn,.nav a{font-family:'Montserrat',sans-serif}
.hl{color:var(--magenta)}
.btn{display:inline-flex;align-items:center;justify-content:center;gap:8px;font-weight:700;font-size:12px;letter-spacing:.5px;text-transform:uppercase;color:var(--white);padding:0 22px;height:36px;border-radius:3px;text-decoration:none;white-space:nowrap}
.btn-orange{background:var(--orange)}
.btn-blue{background:var(--blue)}
.section{position:absolute;left:0;width:1200px}
.section-title{font-size:30px;font-weight:800;color:var(--ink);text-transform:uppercase;text-align:center;line-height:1.25}
.photo{position:absolute}

/* header */
.site-header{top:0;height:128px;background:var(--white)}
.brand{position:absolute;left:152px;top:22px;display:flex;align-items:center;gap:10px}
.brand-mark{width:14px;height:14px;background:var(--magenta)}
.brand-name{font-family:'Montserrat',sans-serif;font-weight:800;font-size:40px;color:var(--purple);line-height:1}
.brand-tag{position:absolute;left:152px;top:72px;font-family:'Montserrat',sans-serif;font-size:11px;font-weight:700;color:var(--purple);letter-spacing:1.5px}
.call{position:absolute;left:600px;top:24px;display:flex;align-items:center;gap:8px;font-size:11px;color:var(--ink)}
.call strong{display:block;color:var(--purple);font-size:13px;font-family:'Montserrat',sans-serif;white-space:nowrap}
.call-icon{width:26px;height:26px;border-radius:50%;background:var(--purple);display:flex;align-items:center;justify-content:center;flex:none}
.head-btns{position:absolute;right:152px;top:26px;display:flex;gap:14px}
.head-btns .btn{height:32px;font-size:11px;padding:0 18px}
.btn-magenta{background:var(--magenta)}
.btn-purple{background:var(--purple)}
.nav{position:absolute;right:152px;top:86px;display:flex;gap:38px}
.nav a{font-size:12px;font-weight:700;text-transform:uppercase;color:var(--ink);text-decoration:none;padding-bottom:8px;white-space:nowrap}
.nav a.active{color:var(--magenta);border-bottom:2px solid var(--magenta)}

/* hero */
.hero{top:128px;height:492px}
.hero-bg{left:0;top:0;width:1200px;height:492px;background:linear-gradient(90deg,#f4f4f6 0%,#eef0f3 35%,#c9cdd3 60%,#8f98a4 100%)}
.hero-copy{position:absolute;left:152px;top:46px;width:480px}
.hero-copy h1{font-size:34px;font-weight:800;line-height:1.14;color:var(--ink);text-transform:uppercase}
.hero-copy p{margin-top:18px;font-size:15px;line-height:1.5;color:var(--text);width:300px}
.hero-actions{margin-top:22px;display:flex;flex-direction:column;gap:20px;align-items:flex-start}

/* lending */
.lending{top:620px;height:640px}
.lending .section-title{margin-top:56px}
.lend-grid{position:absolute;left:152px;top:212px;display:grid;grid-template-columns:repeat(4,212px);grid-auto-rows:168px;gap:16px 16px}
.lend-card{background:var(--white);box-shadow:0 4px 18px rgba(20,20,40,.08);display:flex;flex-direction:column;align-items:center;justify-content:center;gap:18px;font-family:'Montserrat',sans-serif;font-weight:700;font-size:12px;text-transform:uppercase;color:var(--ink)}
.lend-card svg{width:52px;height:52px;fill:none;stroke:var(--purple);stroke-width:2.4;stroke-linecap:round;stroke-linejoin:round}
.lend-card.active{background:var(--magenta);color:var(--white)}
.lend-card.active svg{stroke:var(--white)}

/* about */
.about{top:1260px;height:500px;background:var(--soft)}
.about-photo{left:152px;top:40px;width:428px;height:412px;background:linear-gradient(135deg,#7a6a5e,#b9a895 45%,#5d6f86)}
.about-copy{position:absolute;left:624px;top:52px;width:424px}
.eyebrow{font-family:'Montserrat',sans-serif;font-size:13px;font-weight:700;color:var(--ink);text-transform:uppercase;letter-spacing:.5px}
.about-copy h2{font-size:28px;font-weight:800;color:var(--ink);text-transform:uppercase;line-height:1.2;margin-top:8px}
.about-copy p{font-size:12.5px;line-height:1.6;margin-top:14px}
.tabs{display:flex;gap:18px;margin-top:16px}
.tab{display:flex;align-items:center;gap:6px;font-family:'Montserrat',sans-serif;font-size:10px;font-weight:700;text-transform:uppercase;color:var(--ink);padding:6px 10px;border-radius:3px}
.tab i{width:16px;height:16px;border-radius:50%;border:2px solid var(--purple)}
.tab.active{background:var(--purple);color:var(--white)}
.tab.active i{border-color:var(--white)}
.about-copy .btn{margin-top:22px}

/* lenders */
.lenders{top:1760px;height:500px}
.lenders .section-title{margin-top:126px}
.lender-grid{position:absolute;left:152px;top:240px;width:896px;display:grid;grid-template-columns:repeat(6,1fr);gap:26px 28px}
.lender-badge{height:34px;background:#dfe1e6;border-radius:4px}
.lender-badge.dark{background:#c9ccd3}
.slide-arrow{position:absolute;width:22px;height:22px;fill:none;stroke:#9a9ca6;stroke-width:2.4}
.lenders .btn{position:absolute;left:502px;top:416px;width:196px}

/* services */
.services{top:2260px;height:540px}
.services .section-title{margin-top:60px}
.services .lead{text-align:center;font-size:14px;margin-top:8px}
.service-grid{position:absolute;left:152px;top:196px;display:grid;grid-template-columns:440px 440px;gap:28px 16px}
.service-card{height:120px;background:var(--white);box-shadow:0 4px 18px rgba(20,20,40,.09);display:flex;gap:18px;padding:22px 24px}
.service-icon{flex:none;width:52px;height:52px;border-radius:50%;background:var(--purple);display:flex;align-items:center;justify-content:center}
.service-icon svg{width:26px;height:26px;fill:none;stroke:var(--white);stroke-width:2.2;stroke-linecap:round;stroke-linejoin:round}
.service-card h3{font-size:12px;font-weight:800;color:var(--ink);text-transform:uppercase}
.service-card p{font-size:11.5px;line-height:1.55;margin-top:6px}

/* compare */
.compare{top:2800px;height:680px;background:var(--blue)}
.compare .section-title{color:var(--white);margin-top:60px}
.compare-table{position:absolute;left:152px;top:156px;width:896px;border-collapse:collapse;font-size:13px;color:var(--white)}
.compare-table th{height:44px;font-family:'Montserrat',sans-serif;font-size:12px;font-weight:700}
.compare-table td{height:40px;border-top:1px solid rgba(255,255,255,.18)}
.compare-table td:first-child{padding-left:24px}
.compare-table .col-us{width:160px;text-align:center;background:rgba(255,255,255,.08)}
.compare-table .col-them{width:188px;text-align:center;background:var(--blue-dark)}
.compare-table th.col-us{background:var(--white);color:var(--purple);font-size:16px;font-weight:800}
.compare-table th.col-them{background:#122f66}
.compare-table svg{width:16px;height:16px;fill:none;stroke:var(--white);stroke-width:2;vertical-align:middle}
.compare .btn{position:absolute;left:520px;top:606px;width:160px}

/* testimonials */
.testimonials{top:3480px;height:520px}
.testimonials .section-title{margin-top:72px}
.quote-grid{position:absolute;left:152px;top:180px;display:grid;grid-template-columns:repeat(4,212px);gap:16px}
.quote-card{height:280px;border:1px solid var(--line);padding:20px 18px;background:var(--white)}
.stars{color:var(--orange);font-size:12px;letter-spacing:2px}
.quote-card p{font-size:11px;line-height:1.6;margin-top:10px}
.author{display:flex;align-items:center;gap:10px;margin-top:16px}
.avatar{width:36px;height:36px;border-radius:50%;background:linear-gradient(135deg,#b8bcc6,#8d93a0)}
.author h4{font-size:10.5px;font-weight:800;color:var(--ink);text-transform:uppercase}
.author span{font-size:10px}

/* consultation */
.consult{top:4000px;height:568px}
.consult h2{position:absolute;left:152px;top:56px;font-size:32px;font-weight:800;color:var(--ink);text-transform:uppercase;line-height:1.15}
.consult-photo{left:620px;top:0;width:580px;height:568px;background:linear-gradient(135deg,#cfd3d9,#9aa1ab 50%,#5d6470)}
.lead-form{position:absolute;left:152px;top:176px;width:428px;display:grid;grid-template-columns:1fr 1fr;gap:18px 16px}
.field{height:38px;border:1px solid #d4d6dc;font-size:10px;color:#888b96;text-transform:uppercase;padding:12px 12px;font-family:'Montserrat',sans-serif;font-weight:600}
.field.wide{grid-column:1/3;height:120px}
.lead-form .btn{grid-column:1/2;width:150px}

/* footer */
.site-footer{top:4568px;height:400px;background:var(--black);color:#c7c8ce}
.site-footer .brand{top:56px}
.site-footer .brand-name{color:var(--white)}
.site-footer .brand-tag{top:106px;color:#c7c8ce}
.site-footer .get-touch{position:absolute;left:152px;top:160px}
.foot-col{position:absolute;top:56px}
.foot-col h4{font-family:'Montserrat',sans-serif;font-size:12px;font-weight:800;color:var(--white);text-transform:uppercase;margin-bottom:10px}
.foot-col li{list-style:none;font-size:11.5px;line-height:1.75}
.socials{display:flex;gap:10px}
.socials i{width:26px;height:26px;border-radius:50%;background:var(--white)}
.help{margin-top:20px;font-family:'Montserrat',sans-serif;font-size:11px;font-weight:800;color:var(--white);text-transform:uppercase;line-height:1.4}
.foot-call{margin-top:14px;display:flex;gap:8px;align-items:center;font-size:11px}
.foot-call strong{display:block;color:#8f7bd8;font-family:'Montserrat',sans-serif;font-size:13px;white-space:nowrap}
.copyright{position:absolute;left:0;bottom:22px;width:1200px;text-align:center;font-size:11px;border-top:1px solid #26262c;padding-top:14px}
</style>
</head>
<body>

<header class="section site-header">
  <div class="brand"><span class="brand-mark"></span><span class="brand-name">Vantora</span></div>
  <div class="brand-tag">FINANCIAL SERVICES</div>
  <div class="call">
    <span class="call-icon"><svg width="13" height="13" viewBox="0 0 24 24" fill="#fff"><path d="M6.6 10.8a15 15 0 0 0 6.6 6.6l2.2-2.2c.3-.3.7-.4 1-.2 1.1.4 2.3.6 3.6.6.6 0 1 .4 1 1V20c0 .6-.4 1-1 1A17 17 0 0 1 3 4c0-.6.4-1 1-1h3.5c.6 0 1 .4 1 1 0 1.3.2 2.5.6 3.6.1.3 0 .7-.2 1z"/></svg></span>
    <div>Call us<strong>+61 3 5550 1427</strong></div>
  </div>
  <div class="head-btns">
    <a class="btn btn-magenta" href="#">Contact us</a>
    <a class="btn btn-purple" href="#">Calculators</a>
  </div>
  <nav class="nav">
    <a class="active" href="#">Home Loans</a>
    <a href="#">Refinancing</a>
    <a href="#">Commercial Loans</a>
    <a href="#">Car Loans</a>
    <a href="#">Asset Finance</a>
  </nav>
</header>

<section class="section hero">
  <div class="photo hero-bg" role="img" aria-label="Photo of a client signing mortgage papers beside a small model house"></div>
  <div class="hero-copy">
    <h1>Tailored mortgage<br><span class="hl">broking solutions</span><br>from experienced<br>brokers</h1>
    <p>Tailored mortgage broking solutions from experienced brokers, customized to fit your needs.</p>
    <div class="hero-actions">
      <a class="btn btn-orange" href="#">Get started <svg width="12" height="12" viewBox="0 0 24 24" fill="none" stroke="#fff" stroke-width="3"><path d="M9 5l7 7-7 7"/></svg></a>
      <a class="btn btn-orange" href="#"><svg width="12" height="12" viewBox="0 0 24 24" fill="#fff"><path d="M6.6 10.8a15 15 0 0 0 6.6 6.6l2.2-2.2c.3-.3.7-.4 1-.2 1.1.4 2.3.6 3.6.6.6 0 1 .4 1 1V20c0 .6-.4 1-1 1A17 17 0 0 1 3 4c0-.6.4-1 1-1h3.5c.6 0 1 .4 1 1 0 1.3.2 2.5.6 3.6.1.3 0 .7-.2 1z"/></svg>+61 3 5550 1427</a>
    </div>
  </div>
</section>

<section class="section lending">
  <h2 class="section-title">Comprehensive <span class="hl">lending<br>solutions</span> for every need</h2>
  <div class="lend-grid">
    <div class="lend-card active"><svg viewBox="0 0 48 48"><path d="M6 22L24 8l18 14"/><path d="M11 19v21h26V19"/><path d="M20 40V28h8v12"/></svg>Home Loans</div>
    <div class="lend-card"><svg viewBox="0 0 48 48"><circle cx="24" cy="24" r="16"/><path d="M24 14v20M29 18h-7a3 3 0 0 0 0 6h4a3 3 0 0 1 0 6h-7"/><path d="M40 10v6h-6"/></svg>Refinancing</div>
    <div class="lend-card"><svg viewBox="0 0 48 48"><rect x="8" y="14" width="32" height="24" rx="2"/><path d="M18 14V9h12v5M8 24h32"/></svg>Business</div>
    <div class="lend-card"><svg viewBox="0 0 48 48"><circle cx="14" cy="34" r="7"/><circle cx="36" cy="36" r="5"/><path d="M14 27V16h14l4 10h6v10M21 34h10"/></svg>Agriculture</div>
    <div class="lend-card"><svg viewBox="0 0 48 48"><path d="M8 18l4-9h24l4 9"/><path d="M8 18h32v4a5 5 0 0 1-10 0 5 5 0 0 1-12 0 5 5 0 0 1-10 0z"/><path d="M11 26v14h26V26M20 40v-8h8v8"/></svg>Commercial Loans</div>
    <div class="lend-card"><svg viewBox="0 0 48 48"><path d="M8 30l4-11h24l4 11v8H8z"/><circle cx="15" cy="32" r="2"/><circle cx="33" cy="32" r="2"/><path d="M12 38v3M36 38v3"/></svg>Car Loans</div>
    <div class="lend-card"><svg viewBox="0 0 48 48"><rect x="8" y="16" width="14" height="24"/><rect x="26" y="8" width="14" height="32"/><path d="M12 22h6M12 28h6M30 14h6M30 20h6M30 26h6"/></svg>Asset Finance</div>
    <div class="lend-card"><svg viewBox="0 0 48 48"><rect x="8" y="8" width="13" height="13" rx="2"/><rect x="27" y="8" width="13" height="13" rx="2"/><rect x="8" y="27" width="13" height="13" rx="2"/><rect x="27" y="27" width="13" height="13" rx="2"/></svg>Other Loans</div>
  </div>
</section>

<section class="section about">
  <div class="photo about-photo" role="img" aria-label="Collage of photos of a smiling broker and clients in a meeting"></div>
  <div class="about-copy">
    <div class="eyebrow">About our company</div>
    <h2>Mortgage finance<br>broker in <span class="hl">Melbourne</span></h2>
    <p>We are a Melbourne based broking team helping Australians secure the right home, business and asset finance. We compare lenders for you, explain every option clearly and stay with you from the first chat to settlement and beyond, so your loan keeps working for you.</p>
    <div class="tabs">
      <span class="tab active"><i></i>Our vision</span>
      <span class="tab"><i></i>Our mission</span>
      <span class="tab"><i></i>Our values</span>
    </div>
    <p>Our vision is simple lending for everyone. We want every client to feel confident, informed and supported with a loan that suits their life.</p>
    <a class="btn btn-blue" href="#">More about us <svg width="12" height="12" viewBox="0 0 24 24" fill="none" stroke="#fff" stroke-width="3"><path d="M9 5l7 7-7 7"/></svg></a>
  </div>
</section>

<section class="section lenders">
  <h2 class="section-title">Access over <span class="hl">60 lenders</span> in one place</h2>
  <svg class="slide-arrow" style="left:66px;top:232px" viewBox="0 0 24 24"><path d="M15 5l-7 7 7 7"/></svg>
  <svg class="slide-arrow" style="left:1112px;top:232px" viewBox="0 0 24 24"><path d="M9 5l7 7-7 7"/></svg>
  <div class="lender-grid" aria-label="Lender partner badges">
    <div class="lender-badge"></div><div class="lender-badge dark"></div><div class="lender-badge"></div><div class="lender-badge dark"></div><div class="lender-badge"></div><div class="lender-badge dark"></div>
    <div class="lender-badge dark"></div><div class="lender-badge"></div><div class="lender-badge dark"></div><div class="lender-badge"></div><div class="lender-badge dark"></div><div class="lender-badge"></div>
  </div>
  <a class="btn btn-blue" href="#">Compare rates <svg width="12" height="12" viewBox="0 0 24 24" fill="none" stroke="#fff" stroke-width="3"><path d="M9 5l7 7-7 7"/></svg></a>
</section>

<section class="section services">
  <h2 class="section-title">What we'll do <span class="hl">for you</span></h2>
  <p class="lead">From understanding your goals to settlement and beyond, here is how we'll work together.</p>
  <div class="service-grid">
    <div class="service-card"><span class="service-icon"><svg viewBox="0 0 24 24"><circle cx="12" cy="12" r="9"/><circle cx="12" cy="12" r="4"/></svg></span><div><h3>Understand your goals</h3><p>We start by listening to your plans, budget and timeline so every option we bring fits your needs.</p></div></div>
    <div class="service-card"><span class="service-icon"><svg viewBox="0 0 24 24"><path d="M5 7h14M5 12h14M5 17h9"/></svg></span><div><h3>Provide you with some options</h3><p>We compare loans from many lenders and show you clear choices with rates, fees and features side by side.</p></div></div>
    <div class="service-card"><span class="service-icon"><svg viewBox="0 0 24 24"><path d="M5 12l5 5L19 7"/></svg></span><div><h3>Get it sorted for you</h3><p>We handle the paperwork, talk to the lender and keep you updated until your loan is approved and settled.</p></div></div>
    <div class="service-card"><span class="service-icon"><svg viewBox="0 0 24 24"><path d="M4 13l4 4 6-2 6-6-4-4-6 2z"/></svg></span><div><h3>Help you save</h3><p>We review your loan over time and help you refinance when a better deal can save you money.</p></div></div>
  </div>
</section>

<section class="section compare">
  <h2 class="section-title">What makes us different?</h2>
  <table class="compare-table">
    <thead><tr><th></th><th class="col-us">Vantora</th><th class="col-them">Banks &amp; lenders</th></tr></thead>
    <tbody>
      <tr><td>Your own personal, non-bank affiliated loan expert</td><td class="col-us"><svg viewBox="0 0 24 24"><circle cx="12" cy="12" r="9"/><path d="M8 12l3 3 5-6"/></svg></td><td class="col-them"><svg viewBox="0 0 24 24"><path d="M7 7l10 10M17 7L7 17"/></svg></td></tr>
      <tr><td>Free for you</td><td class="col-us"><svg viewBox="0 0 24 24"><circle cx="12" cy="12" r="9"/><path d="M8 12l3 3 5-6"/></svg></td><td class="col-them"><svg viewBox="0 0 24 24"><path d="M7 7l10 10M17 7L7 17"/></svg></td></tr>
      <tr><td>We work in your best interests (we're not owned by a bank)</td><td class="col-us"><svg viewBox="0 0 24 24"><circle cx="12" cy="12" r="9"/><path d="M8 12l3 3 5-6"/></svg></td><td class="col-them"><svg viewBox="0 0 24 24"><path d="M7 7l10 10M17 7L7 17"/></svg></td></tr>
      <tr><td>Fast turnaround times</td><td class="col-us"><svg viewBox="0 0 24 24"><circle cx="12" cy="12" r="9"/><path d="M8 12l3 3 5-6"/></svg></td><td class="col-them"><svg viewBox="0 0 24 24"><path d="M7 7l10 10M17 7L7 17"/></svg></td></tr>
      <tr><td>Access to over 60+ banks and lenders in one place</td><td class="col-us"><svg viewBox="0 0 24 24"><circle cx="12" cy="12" r="9"/><path d="M8 12l3 3 5-6"/></svg></td><td class="col-them"><svg viewBox="0 0 24 24"><path d="M7 7l10 10M17 7L7 17"/></svg></td></tr>
      <tr><td>Ongoing support and guidance once your loan has settled</td><td class="col-us"><svg viewBox="0 0 24 24"><circle cx="12" cy="12" r="9"/><path d="M8 12l3 3 5-6"/></svg></td><td class="col-them"><svg viewBox="0 0 24 24"><path d="M7 7l10 10M17 7L7 17"/></svg></td></tr>
    </tbody>
  </table>
  <a class="btn btn-orange" href="#">Get started <svg width="12" height="12" viewBox="0 0 24 24" fill="none" stroke="#fff" stroke-width="3"><path d="M9 5l7 7-7 7"/></svg></a>
</section>

<section class="section testimonials">
  <h2 class="section-title">Customer <span class="hl">testimonials</span></h2>
  <svg class="slide-arrow" style="left:66px;top:308px;stroke:var(--blue)" viewBox="0 0 24 24"><path d="M15 5l-7 7 7 7"/></svg>
  <svg class="slide-arrow" style="left:1112px;top:308px;stroke:var(--blue)" viewBox="0 0 24 24"><path d="M9 5l7 7-7 7"/></svg>
  <div class="quote-grid">
    <div class="quote-card"><div class="stars">★★★★★</div><p>The team made buying our first home so easy. They explained every step, found us a great rate and kept us updated the whole way through. We could not have asked for better help.</p><div class="author"><span class="avatar"></span><div><h4>Liam Carter</h4><span>2 days ago</span></div></div></div>
    <div class="quote-card"><div class="stars">★★★★★</div><p>Refinancing felt daunting until we called. Within weeks we had a lower rate and a clear plan. Friendly, fast and honest service that saved us real money every month.</p><div class="author"><span class="avatar"></span><div><h4>Liam Carter</h4><span>2 days ago</span></div></div></div>
    <div class="quote-card"><div class="stars">★★★★★</div><p>They sorted finance for our new farm equipment quickly and without fuss. Great knowledge of business lending and always available to answer our questions.</p><div class="author"><span class="avatar"></span><div><h4>Liam Carter</h4><span>2 days ago</span></div></div></div>
    <div class="quote-card"><div class="stars">★★★★★</div><p>Professional from start to finish. They compared many lenders for our car loan and found an option that suited our budget perfectly. Highly recommend.</p><div class="author"><span class="avatar"></span><div><h4>Liam Carter</h4><span>2 days ago</span></div></div></div>
  </div>
</section>

<section class="section consult">
  <h2>Request a<br><span class="hl">free consultation</span></h2>
  <form class="lead-form">
    <div class="field">First name</div>
    <div class="field">Last name</div>
    <div class="field">Phone</div>
    <div class="field">Email</div>
    <div class="field wide">Message</div>
    <a class="btn btn-orange" href="#">Send message</a>
  </form>
  <div class="photo consult-photo" role="img" aria-label="Photo of a broker shaking hands with clients across a desk"></div>
</section>

<footer class="section site-footer">
  <div class="brand"><span class="brand-mark"></span><span class="brand-name">Vantora</span></div>
  <div class="brand-tag">FINANCIAL SERVICES</div>
  <a class="btn btn-blue get-touch" href="#">Get in touch today <svg width="12" height="12" viewBox="0 0 24 24" fill="none" stroke="#fff" stroke-width="3"><path d="M9 5l7 7-7 7"/></svg></a>
  <div class="foot-col" style="left:452px"><h4>Menu</h4><ul><li>Home Loans</li><li>Refinancing</li><li>Business</li><li>Agriculture</li><li>Commercial Loans</li><li>Car Loans</li><li>Asset Finance</li></ul></div>
  <div class="foot-col" style="left:632px"><h4>Calculators &amp; Tools</h4><ul><li>Compare Rates</li><li>Calculators</li></ul><h4 style="margin-top:18px">About</h4><ul><li>Our Team</li><li>Working With Us</li><li>Our Partners</li></ul></div>
  <div class="foot-col" style="left:852px"><h4>Follow us</h4><div class="socials"><i></i><i></i><i></i><i></i></div>
    <div class="help">We're here to help.<br>Contact us</div>
    <div class="foot-call"><span class="call-icon"><svg width="13" height="13" viewBox="0 0 24 24" fill="#fff"><path d="M6.6 10.8a15 15 0 0 0 6.6 6.6l2.2-2.2c.3-.3.7-.4 1-.2 1.1.4 2.3.6 3.6.6.6 0 1 .4 1 1V20c0 .6-.4 1-1 1A17 17 0 0 1 3 4c0-.6.4-1 1-1h3.5c.6 0 1 .4 1 1 0 1.3.2 2.5.6 3.6.1.3 0 .7-.2 1z"/></svg></span><div>Call us<strong>+61 3 5550 1427</strong></div></div>
  </div>
  <div class="copyright">Copyright © 2025 All Rights Reserved</div>
</footer>

</body>
</html>
```